Verdana Harvest Co - Business Card Design Project

We need business cards for our business. We grow roots and fruits in Central and South America, we import and distribute in FL, USA. We do fresh and frozen products.

Target Market(s)

Small and big supermarkets, wholesalers, traders, distributors, etc

Industry/Entity Type

Business

```html
<!DOCTYPE html>
<html lang="en">
<head>
<meta charset="utf-8">
<title>Verdana Harvest Co – Business Cards</title>
<link rel="stylesheet" href="https://fonts.googleapis.com/css2?family=Montserrat:wght@600;700&family=Cinzel:wght@600&family=Arimo:wght@400&display=swap">
<style>
  :root {
    --bg: #2a2a2a;
    --card: #ffffff;
    --orange: #d9820f;
    --green: #4f5e2c;
    --ink: #1e1e1e;
    --muted: #333333;
  }
  * { box-sizing: border-box; margin: 0; padding: 0; }
  html, body { width: 1200px; height: 997px; overflow: hidden; }
  body {
    background: var(--bg);
    position: relative;
    font-family: "Arimo", Arial, sans-serif;
  }
  .card {
    position: absolute;
    left: 300px;
    width: 600px;
    height: 343px;
    background: var(--card);
    overflow: hidden;
  }
  .card--back { top: 100px; }
  .card--front { top: 554px; }

  .card__band {
    position: absolute;
    left: 0; bottom: 0;
    width: 600px; height: 32px;
  }
  .band-orange { fill: var(--orange); }
  .band-green { fill: var(--green); }

  .brand {
    position: absolute;
    display: flex;
    align-items: center;
    gap: 12px;
    font-family: "Montserrat", sans-serif;
    font-weight: 700;
    color: var(--orange);
  }
  .brand__dot {
    width: 18px; height: 18px;
    border-radius: 50%;
    background: var(--green);
  }
  .brand__name {
    font-size: 30px;
    letter-spacing: 0.5px;
    line-height: 1;
  }
  .card--back .brand { left: 0; right: 0; top: 135px; justify-content: center; }
  .card--back .brand__name { font-size: 34px; }
  .card--front .brand { left: 190px; top: 56px; }

  .person {
    position: absolute;
    left: 58px;
    top: 198px;
  }
  .person__name {
    font-family: "Cinzel", serif;
    font-weight: 600;
    font-size: 21px;
    color: var(--ink);
    letter-spacing: 0.5px;
  }
  .person__role {
    font-family: "Montserrat", sans-serif;
    font-weight: 700;
    font-size: 14px;
    color: var(--green);
    letter-spacing: 0.5px;
    margin-top: 2px;
  }

  .divider {
    position: absolute;
    left: 300px;
    top: 150px;
    width: 3px;
    height: 110px;
    background: linear-gradient(to bottom, rgba(217,130,15,0), var(--orange) 30%, var(--orange) 70%, rgba(217,130,15,0));
  }

  .contacts {
    position: absolute;
    left: 326px;
    top: 158px;
    list-style: none;
  }
  .contacts__item {
    display: flex;
    align-items: center;
    gap: 16px;
    height: 24px;
    font-size: 14px;
    color: var(--muted);
  }
  .contacts__icon { width: 13px; height: 13px; fill: var(--orange); flex: none; }
</style>
</head>
<body>

  <section class="card card--back" aria-label="Card back">
    <div class="brand">
      <span class="brand__dot"></span>
      <span class="brand__name">Verdana Harvest Co</span>
    </div>
    <svg class="card__band" viewBox="0 0 600 32" aria-hidden="true">
      <rect class="band-orange" x="0" y="21" width="430" height="11"/>
      <path class="band-green" d="M442,32 Q442,6 470,6 L600,6 L600,32 Z"/>
    </svg>
  </section>

  <section class="card card--front" aria-label="Card front">
    <div class="brand">
      <span class="brand__dot"></span>
      <span class="brand__name">Verdana Harvest Co</span>
    </div>

    <div class="person">
      <p class="person__name">MARCO DELGADO</p>
      <p class="person__role">MANAGING DIRECTOR</p>
    </div>

    <div class="divider"></div>

    <ul class="contacts">
      <li class="contacts__item">
        <svg class="contacts__icon" viewBox="0 0 16 16" aria-hidden="true"><path d="M3 1h3l1.5 4-2 1.3a9 9 0 0 0 4.2 4.2L11 8.5l4 1.5v3a2 2 0 0 1-2 2A13 13 0 0 1 1 3a2 2 0 0 1 2-2z"/></svg>
        <span>+1 305 555 0148</span>
      </li>
      <li class="contacts__item">
        <svg class="contacts__icon" viewBox="0 0 16 16" aria-hidden="true"><path d="M1 3h14v10H1z M2 4l6 5 6-5" stroke="#fff" stroke-width="1.2"/></svg>
        <span>marco@verdanaharvest.com</span>
      </li>
      <li class="contacts__item">
        <svg class="contacts__icon" viewBox="0 0 16 16" aria-hidden="true"><path d="M6.5 9.5l3-3M5 8l-2 2a2.5 2.5 0 0 0 3.5 3.5l2-2M11 8l2-2A2.5 2.5 0 0 0 9.5 2.5l-2 2" fill="none" stroke="var(--orange)" stroke-width="1.8" stroke-linecap="round"/></svg>
        <span>www.verdanaharvest.com</span>
      </li>
      <li class="contacts__item">
        <svg class="contacts__icon" viewBox="0 0 16 16" aria-hidden="true"><circle cx="8" cy="8" r="6"/></svg>
        <span>@verdanaharvest</span>
      </li>
    </ul>

    <svg class="card__band" viewBox="0 0 600 32" aria-hidden="true">
      <rect class="band-orange" x="0" y="21" width="430" height="11"/>
      <path class="band-green" d="M442,32 Q442,6 470,6 L600,6 L600,32 Z"/>
    </svg>
  </section>

</body>
</html>
```